Copper Field Agency Website - Wordpress Web UPDATED BRIEF

FINAL LOGO UPLOADED - please look to this as reference for how we would like the site to look and feel.

We are a digital marketing agency - looking to have a new website built. We are looking for a simple one page feel of site that will allow us to grow it later. (Feel free to take some liberties with that if your imagination veers off) Must be very, playful, bold, sleek and easily integrate video. Wordpress only.

Overview:

Copper Field is a creative constellation. We are built on what's great about the shared economy. With access to thousands of content creators, designers, technicians, writers, strategists and other creatives around the world, we are built differently than a traditional “brick and mortar” Marketing Agency. We provide the traditional services our clients have come to expect, without the “5X factor” of covering the overhead common in the old agency model. We believe even better work can be created in collaboration with our clients and by passing those savings back to them for their use. Our clients pay for our art, our work and our passion –not our furniture.

"Copper Field, Let's Build Together"

Target Market(s)

companies looking for creative agency help, video production, creative consulting and coaching

Industry/Entity Type

Digital Marketing

Coding

Coded - Design and coding required

Number of Pages Required

1 page

Font styles to use
Sans Serif

Colors
3277b5
33a6d7
ec1f27

Requirements
Must have
• Wordpress design is a must. Looking for a one sheet homepage - with sections that are all on the main front page. We will have videos to embed, and should be able to have client logos and easy access to show a variety of our creative work.
• Please look to the logo for how we would like the site to feel.
• Please think "icon process flow" instead of blocks of text (which we used to have). Use the text to explain what the process flow should represent - don't actually copy paste the text but show it visually in icons.
Nice to have
• innovation around how we show video content. solid colors complementary to our palette and aesthetic.
Should not have
• Standard HTML coding

```html
<!DOCTYPE html>
<html lang="en">
<head>
<meta charset="utf-8">
<title>Copper Field Agency</title>
<link href="https://fonts.googleapis.com/css2?family=Roboto:wght@400;500;700&family=Open+Sans:ital,wght@0,400;0,600;1,400;1,600&display=swap" rel="stylesheet">
<style>
:root{
  --blue:#3277b5;
  --sky:#33a6d7;
  --red:#ec1f27;
  --ink:#2e2e2e;
  --grey:#6b6b6b;
  --line:#d9d9d9;
  --mist:#eef2f7;
  --footer:#1f1f1f;
  --white:#ffffff;
}
*{margin:0;padding:0;box-sizing:border-box}
html,body{width:1200px;height:3948px;overflow:hidden}
body{position:relative;background:var(--white);font-family:'Open Sans',sans-serif;color:var(--ink)}
.section{position:absolute;left:0;width:1200px}
.section-title{position:absolute;left:0;width:1200px;text-align:center;font-family:'Roboto',sans-serif;font-weight:700;font-size:44px;color:var(--ink)}

/* Hero */
.hero{top:0;height:676px;background:linear-gradient(160deg,#5a88c9 0%,#3f6fb8 45%,#2c58a0 100%)}
.hero-photo{position:absolute;inset:0;background:radial-gradient(ellipse at 50% 75%,rgba(255,255,255,.28),rgba(255,255,255,0) 55%)}
.brand{position:absolute;left:96px;top:10px;display:flex;align-items:center;gap:10px}
.brand-mark{width:44px;height:44px;border-radius:50%;background:var(--red)}
.brand-name{font-family:'Roboto',sans-serif;font-weight:700;font-size:26px;color:var(--white)}
.nav{position:absolute;left:488px;top:56px;display:flex;gap:26px;font-family:'Roboto',sans-serif;font-size:15px;font-weight:500;color:var(--white)}
.nav .active{color:var(--red)}
.hero-title{position:absolute;top:156px;left:0;width:1200px;text-align:center;font-family:'Roboto',sans-serif;font-weight:700;font-size:50px;color:var(--white)}
.hero-video{position:absolute;top:244px;left:0;width:1200px;text-align:center;font-family:'Roboto',sans-serif;font-size:22px;font-weight:500;color:var(--white)}
.hero-video svg{vertical-align:-4px;margin-right:10px}
.hero-arrow{position:absolute;top:306px}

/* About */
.about{top:676px;height:720px}
.about-photo{position:absolute;left:112px;top:104px;width:460px;height:440px;background:linear-gradient(135deg,#cfd6dd,#8c97a3)}
.about-card{position:absolute;left:520px;top:152px;width:568px;height:340px;background:var(--white);border:1px solid var(--line);border-radius:6px;box-shadow:0 4px 14px rgba(0,0,0,.12);padding:36px 40px}
.about-card h2{font-family:'Roboto',sans-serif;font-weight:700;font-size:44px;color:var(--ink);margin-bottom:14px}
.about-card p{font-size:12.5px;line-height:1.75;color:var(--grey)}

/* Services */
.services{top:1396px;height:576px;background:var(--mist);overflow:hidden}
.services .section-title{top:84px}
.process{position:absolute;left:0;top:0}
.step-label{font-family:'Roboto',sans-serif;font-size:17px;font-weight:500;fill:var(--ink)}

/* Works */
.works{top:1972px;height:868px}
.works .section-title{top:100px}
.work-tile{position:absolute;width:316px;height:262px}

/* Testimonials */
.testimonials{top:2840px;height:348px;background:var(--red);color:var(--white)}
.quote-mark{position:absolute;left:186px;top:40px;font-family:'Roboto',sans-serif;font-weight:700;font-size:150px;line-height:1}
.testimonials h2{position:absolute;left:112px;top:190px;width:310px;text-align:center;font-family:'Roboto',sans-serif;font-weight:700;font-size:40px}
.testimonial-text{position:absolute;left:440px;top:76px;width:560px;font-style:italic;font-size:24px;line-height:1.6}
.testimonial-author{position:absolute;left:440px;top:226px;font-weight:600;font-style:italic;font-size:22px}
.testimonial-nav{position:absolute;left:1024px;top:226px;display:flex;gap:8px}

/* Clients */
.clients{top:3188px;height:368px}
.clients .section-title{top:84px}
.client-logo{position:absolute;top:184px;width:188px;height:88px;border:2px solid var(--line);display:flex;align-items:center;justify-content:center;font-family:'Roboto',sans-serif;font-weight:700;font-size:28px;color:#9a9a9a}
.client-arrow{position:absolute;top:212px}

/* Footer */
.footer{top:3556px;height:392px;background:var(--footer);color:#cfcfcf}
.footer-brand{position:absolute;left:150px;top:60px;width:140px;text-align:center}
.footer-brand .brand-mark{width:96px;height:96px;margin:0 auto 12px}
.footer-brand .brand-name{font-size:24px}
.footer-col{position:absolute;top:72px;list-style:none;font-size:13px;line-height:2.25}
.footer-col li{display:flex;align-items:center;gap:12px}
.social-dot{width:16px;height:16px;background:#cfcfcf}
.copyright{position:absolute;left:0;top:336px;width:1200px;text-align:center;font-size:13px;color:#a8a8a8}
</style>
</head>
<body>

<header class="section hero">
  <div class="hero-photo" role="img" aria-label="Photo of a workspace desk seen from above with a laptop, coffee cup, notebook and sticky notes"></div>
  <div class="brand"><span class="brand-mark"></span><span class="brand-name">Copper Field</span></div>
  <nav class="nav">
    <span class="active">Home</span><span>About</span><span>Services</span><span>Work</span><span>Testimonials</span><span>Clients</span><span>Contact</span>
    <svg width="16" height="16" viewBox="0 0 16 16" fill="none" stroke="#fff" stroke-width="2"><circle cx="6.5" cy="6.5" r="5"/><line x1="10.5" y1="10.5" x2="15" y2="15"/></svg>
  </nav>
  <h1 class="hero-title">Copper Field, Let's Build Together</h1>
  <div class="hero-video"><svg width="24" height="24" viewBox="0 0 24 24"><circle cx="12" cy="12" r="10" fill="none" stroke="#fff" stroke-width="2"/><path d="M10 7.5l6 4.5-6 4.5z" fill="#fff"/></svg>Watch Our Videos</div>
  <svg class="hero-arrow" style="left:36px" width="28" height="44" viewBox="0 0 28 44"><path d="M22 4L6 22l16 18" fill="none" stroke="#fff" stroke-width="4" opacity=".8"/></svg>
  <svg class="hero-arrow" style="right:36px" width="28" height="44" viewBox="0 0 28 44"><path d="M6 4l16 18L6 40" fill="none" stroke="#fff" stroke-width="4" opacity=".8"/></svg>
</header>

<section class="section about">
  <div class="about-photo" role="img" aria-label="Photo of a smiling team member at an office desk"></div>
  <div class="about-card">
    <h2>About Us</h2>
    <p>Copper Field is a creative constellation. We are built on what's great about the shared economy. With access to thousands of content creators, designers, technicians, writers, strategists and other creatives around the world, we are built differently than a traditional “brick and mortar” Marketing Agency. We provide the traditional services our clients have come to expect, without the “5X factor” of covering the overhead common in the old agency model. We believe even better work can be created in collaboration with our clients and by passing those savings back to them for their use. Our clients pay for our art, our work and our passion – not our furniture.</p>
  </div>
</section>

<section class="section services">
  <h2 class="section-title">Our Services</h2>
  <svg class="process" width="1200" height="576" viewBox="0 1396 1200 576">
    <path d="M280 1972 A320 320 0 0 1 920 1972" fill="none" stroke="#c4cfdc" stroke-width="3" stroke-dasharray="8 8"/>
    <g role="img" aria-label="Illustration of the agency mascot character">
      <path d="M380 1972 A220 220 0 0 1 820 1972 Z" fill="var(--blue)"/>
      <path d="M420 1972 A180 180 0 0 1 780 1972 Z" fill="var(--sky)" opacity=".55"/>
    </g>
    <g fill="#fff" stroke="var(--red)" stroke-width="3">
      <circle cx="600" cy="1652" r="34"/><circle cx="440" cy="1695" r="34"/><circle cx="760" cy="1695" r="34"/>
      <circle cx="323" cy="1812" r="34"/><circle cx="877" cy="1812" r="34"/><circle cx="285" cy="1916" r="34"/><circle cx="915" cy="1916" r="34"/>
    </g>
    <g fill="var(--red)" stroke="none">
      <!-- gear -->
      <circle cx="600" cy="1652" r="11"/><rect x="596" y="1634" width="8" height="36"/><rect x="582" y="1648" width="36" height="8"/>
      <circle cx="600" cy="1652" r="4" fill="#fff"/>
      <!-- document -->
      <path d="M428 1679h18l8 8v24h-26z"/>
      <rect x="433" y="1692" width="16" height="2.5" fill="#fff"/><rect x="433" y="1699" width="16" height="2.5" fill="#fff"/>
      <!-- megaphone -->
      <path d="M746 1689h8l16-9v30l-16-9h-8z"/><rect x="752" y="1701" width="5" height="10"/>
      <!-- bulb / strategy -->
      <circle cx="323" cy="1806" r="11"/><rect x="318" y="1818" width="10" height="8"/>
      <!-- paid media screen -->
      <rect x="861" y="1800" width="32" height="22" rx="2"/><path d="M873 1805l9 6-9 6z" fill="#fff"/>
      <!-- coaching chat -->
      <path d="M901 1904h28v18h-16l-7 6v-6h-5z"/>
    </g>
    <!-- discovery magnifier -->
    <circle cx="281" cy="1912" r="9" fill="none" stroke="var(--red)" stroke-width="4"/>
    <line x1="288" y1="1919" x2="297" y2="1928" stroke="var(--red)" stroke-width="4"/>
    <text class="step-label" x="600" y="1592" text-anchor="middle">Project Management</text>
    <text class="step-label" x="392" y="1678" text-anchor="end">Content</text>
    <text class="step-label" x="808" y="1678">Production</text>
    <text class="step-label" x="274" y="1774" text-anchor="end">Strategy</text>
    <text class="step-label" x="926" y="1774">Paid Media</text>
    <text class="step-label" x="236" y="1886" text-anchor="end">Discovery</text>
    <text class="step-label" x="964" y="1886">Coaching</text>
  </svg>
</section>

<section class="section works">
  <h2 class="section-title">Our Creative Works</h2>
  <div class="work-tile" style="left:112px;top:216px;background:linear-gradient(135deg,#3a6fb8,#1d3f7a)" role="img" aria-label="Photo of a hand touching a digital interface"></div>
  <div class="work-tile" style="left:440px;top:216px;background:linear-gradient(135deg,#6ea8e0,#2a5d9f)" role="img" aria-label="Photo of hands typing on a laptop keyboard"></div>
  <div class="work-tile" style="left:768px;top:216px;background:linear-gradient(135deg,#5c9bd8,#1f4d8c)" role="img" aria-label="Photo of a tablet surrounded by network icons"></div>
  <div class="work-tile" style="left:112px;top:496px;background:linear-gradient(135deg,#2c4f82,#13294d)" role="img" aria-label="Photo of a monitor showing analytics dashboards"></div>
  <div class="work-tile" style="left:440px;top:496px;background:linear-gradient(135deg,#2f6bb0,#0f2a55)" role="img" aria-label="Photo of a businessman touching a glowing screen"></div>
  <div class="work-tile" style="left:768px;top:496px;background:linear-gradient(135deg,#9aa4ad,#5d6770)" role="img" aria-label="Photo of a digital marketing concept with a laptop"></div>
</section>

<section class="section testimonials">
  <div class="quote-mark">“</div>
  <h2>Testimonials</h2>
  <p class="testimonial-text">Copper Field is proving to be a force in the creative consulting industry and we look forward to collaborating with them again in the future.</p>
  <p class="testimonial-author">- Daniel Reyes</p>
  <div class="testimonial-nav">
    <svg width="28" height="28" viewBox="0 0 28 28"><circle cx="14" cy="14" r="13" fill="#fff"/><path d="M16 8l-6 6 6 6" fill="none" stroke="var(--red)" stroke-width="3"/></svg>
    <svg width="28" height="28" viewBox="0 0 28 28"><circle cx="14" cy="14" r="13" fill="#fff"/><path d="M12 8l6 6-6 6" fill="none" stroke="var(--red)" stroke-width="3"/></svg>
  </div>
</section>

<section class="section clients">
  <h2 class="section-title">Our Clients</h2>
  <svg class="client-arrow" style="left:40px" width="20" height="34" viewBox="0 0 20 34"><path d="M16 3L4 17l12 14" fill="none" stroke="#9a9a9a" stroke-width="3"/></svg>
  <div class="client-logo" style="left:112px">Northway</div>
  <div class="client-logo" style="left:312px">Northway</div>
  <div class="client-logo" style="left:512px">Northway</div>
  <div class="client-logo" style="left:712px">Northway</div>
  <div class="client-logo" style="left:904px">Northway</div>
  <svg class="client-arrow" style="right:40px" width="20" height="34" viewBox="0 0 20 34"><path d="M4 3l12 14L4 31" fill="none" stroke="#9a9a9a" stroke-width="3"/></svg>
</section>

<footer class="section footer">
  <div class="footer-brand"><div class="brand-mark"></div><div class="brand-name">Copper Field</div></div>
  <ul class="footer-col" style="left:440px"><li>About</li><li>Services</li><li>Work</li><li>Testimonials</li><li>Clients</li><li>Contact</li></ul>
  <ul class="footer-col" style="left:648px"><li>Terms &amp; Conditions</li><li>Returns</li><li>Privacy Policy</li><li>Site Map</li></ul>
  <ul class="footer-col" style="left:888px"><li><span class="social-dot"></span>Chirpline</li><li><span class="social-dot"></span>Friendhub</li><li><span class="social-dot"></span>Reelcast</li></ul>
  <p class="copyright">Copyright © 2015, Copper Field. All Rights Reserved.</p>
</footer>

</body>
</html>
```